A resume/portfolio website for myself

I'm an independent software contractor, architect, tech trainer. I need a web site to present myself. Many ready to use portfolio designs are too artistic and focused on presenting design skills of the person. I like a nice website but the content should be a little less graphic than if you would present a graphic designer. Content could be presentation of me, core skill qualities and services and resume. Potentially a page with my tech courses in the longer run

```html
<!DOCTYPE html>
<html lang="en">
<head>
<meta charset="utf-8">
<title>Jonas Elmgaard — Resume</title>
<link rel="stylesheet" href="https://fonts.googleapis.com/css2?family=Montserrat:wght@500;600&family=Roboto:ital,wght@0,300;0,400;0,500;1,300;1,400&display=swap">
<style>
:root{
  --orange:#ec6c00;
  --orange-ring:#f28a00;
  --ink:#111;
  --body:#555;
  --muted:#666;
  --dark:#1d1d1d;
  --white:#fff;
  --ring-gap:#ccc;
}
*{box-sizing:border-box;margin:0;padding:0}
html,body{width:1200px;height:2671px;overflow:hidden;background:var(--white)}
body{font-family:Roboto,sans-serif;color:var(--ink);position:relative}
.hero{position:absolute;left:0;top:0;width:1200px;height:692px;background:var(--orange);color:var(--white)}
.social{position:absolute;left:86px;top:15px;display:flex;gap:29px}
.social span{width:14px;height:14px;border-radius:50%;background:var(--white);display:block}
.download{position:absolute;left:837px;top:0;width:275px;height:46px;background:var(--white);border-radius:0 0 6px 6px;color:var(--orange);font:500 17px Roboto,sans-serif;display:flex;align-items:center;justify-content:center;gap:10px;letter-spacing:.2px}
.portrait-band{position:absolute;left:0;top:111px;width:508px;height:470px;background:var(--dark);border-radius:0 235px 235px 0}
.portrait{position:absolute;left:59px;top:131px;width:430px;height:430px;border-radius:50%;background:radial-gradient(circle at 45% 40%,#d9d9d9,#9a9a9a 60%,#5e5e5e)}
.name{position:absolute;left:536px;top:100px;font:600 73px/1 Montserrat,sans-serif;letter-spacing:1px}
.tagline{position:absolute;left:541px;top:186px;width:580px;font:500 30px/41px Roboto,sans-serif}
.subline{position:absolute;left:542px;top:282px;font:italic 300 22px Roboto,sans-serif}
.contact{position:absolute;left:542px;top:335px;display:flex;gap:32px;font:400 22px Roboto,sans-serif;align-items:center}
.contact span{display:flex;align-items:center;gap:13px}
.help-title{position:absolute;left:541px;top:404px;font:500 28px Montserrat,sans-serif;letter-spacing:.3px}
.help-list{position:absolute;left:542px;top:459px;list-style:none;font:400 16.5px Roboto,sans-serif}
.help-list li{height:33px;display:flex;align-items:center;gap:11px}
.nav{position:absolute;left:0;top:692px;width:1200px;height:61px;background:#000;display:flex;justify-content:center;align-items:center;gap:60px;color:var(--white);font:400 16.5px Roboto,sans-serif}
.section-title{position:absolute;left:90px;font:400 22px Roboto,sans-serif;color:var(--ink)}
.timeline{position:absolute;left:99px;top:916px;width:2px;height:1012px;background:var(--orange)}
.job{position:absolute;left:90px;width:1010px}
.job .dot{position:absolute;left:0;top:2px;width:20px;height:20px;border:2px solid var(--orange);border-radius:50%;background:var(--white)}
.job .dot::after{content:"";position:absolute;left:4px;top:4px;width:8px;height:8px;border-radius:50%;background:var(--orange)}
.job h3{margin-left:30px;font:500 16.5px Roboto,sans-serif}
.job .date{margin:9px 0 0 31px;font:300 14px Roboto,sans-serif;color:var(--muted)}
.job .role{margin:20px 0 0 30px;font:italic 400 14.5px Roboto,sans-serif;color:#333}
.job p{margin:18px 0 0 31px;font:400 15.5px/27px Roboto,sans-serif;color:var(--body)}
.cols{position:absolute;left:90px;display:flex;width:1040px}
.col{width:390px}
.col h4{font:500 16.5px Roboto,sans-serif;color:var(--orange)}
.col .desc{margin-top:8px;width:250px;font:italic 300 13.5px/21px Roboto,sans-serif;color:#444}
.col .years{margin-top:11px;font:300 14px Roboto,sans-serif;color:var(--muted)}
.ring{display:block;margin-bottom:12px}
.touch{position:absolute;left:91px;top:2454px;width:1030px;font:400 17.5px/31px Roboto,sans-serif;color:var(--body)}
.footer{position:absolute;left:0;top:2628px;width:1200px;text-align:center;font:400 11.5px Roboto,sans-serif;color:var(--muted)}
</style>
</head>
<body>
<header class="hero">
  <div class="social" aria-label="Social profiles"><span></span><span></span><span></span><span></span><span></span></div>
  <div class="download">
    <svg width="18" height="18" viewBox="0 0 18 18" fill="var(--orange)"><path d="M7 1h4v7h3l-5 5-5-5h3z"/><path d="M1 12h3v3h10v-3h3v5H1z"/></svg>
    DOWNLOAD MY RESUME
  </div>
  <div class="portrait-band"></div>
  <div class="portrait" role="img" aria-label="Black and white portrait photo of Jonas Elmgaard"></div>
  <h1 class="name">Jonas Elmgaard</h1>
  <p class="tagline">Lorem ipsum dolor sit amet, consectetur adipiscing</p>
  <p class="subline">Lorem ipsum dolor sit amet, consectetur</p>
  <div class="contact">
    <span><svg width="23" height="17" viewBox="0 0 23 17" fill="#fff"><path d="M0 0h23v2l-11.5 7L0 2z"/><path d="M0 4.5l11.5 7 11.5-7V17H0z"/></svg>hello@elmgaard.dev</span>
    <span><svg width="20" height="20" viewBox="0 0 20 20" fill="#fff"><path d="M4 1l4 4-2 3c1.5 3 3 4.5 6 6l3-2 4 4-3 3C8 18 2 12 1 4z"/></svg>+8 555 010 4477</span>
  </div>
  <h2 class="help-title">I can help with the following</h2>
  <ul class="help-list">
    <li><svg width="16" height="15" viewBox="0 0 16 15"><rect x="1" y="2" width="11" height="11" rx="2" fill="none" stroke="#fff" stroke-width="1.8"/><path d="M4 7l3 3 8-8" fill="none" stroke="#fff" stroke-width="2"/></svg>Lorem ipsum dolor sit amet, consectetur adipiscing elit, sed do</li>
    <li><svg width="16" height="15" viewBox="0 0 16 15"><rect x="1" y="2" width="11" height="11" rx="2" fill="none" stroke="#fff" stroke-width="1.8"/><path d="M4 7l3 3 8-8" fill="none" stroke="#fff" stroke-width="2"/></svg>Lorem ipsum dolor sit amet, consectetur adipiscing elit, sed do</li>
    <li><svg width="16" height="15" viewBox="0 0 16 15"><rect x="1" y="2" width="11" height="11" rx="2" fill="none" stroke="#fff" stroke-width="1.8"/><path d="M4 7l3 3 8-8" fill="none" stroke="#fff" stroke-width="2"/></svg>Lorem ipsum dolor sit amet, consectetur adipiscing elit, sed do</li>
    <li><svg width="16" height="15" viewBox="0 0 16 15"><rect x="1" y="2" width="11" height="11" rx="2" fill="none" stroke="#fff" stroke-width="1.8"/><path d="M4 7l3 3 8-8" fill="none" stroke="#fff" stroke-width="2"/></svg>Lorem ipsum dolor sit amet, consectetur adipiscing elit, sed do</li>
  </ul>
</header>

<nav class="nav"><span>Experience</span><span>Education</span><span>Skills</span><span>Accomplishments</span><span>Portfolio</span><span>Contact</span></nav>

<h2 class="section-title" style="top:854px">Work Experiences</h2>
<div class="timeline"></div>
<div class="job" style="top:906px"><span class="dot"></span><h3>Lorem ipsum dolor</h3><div class="date">Apr 2020 - Present</div><div class="role">Lorem ipsum dolor sit amet, consectetur adipiscing elit, sed do eiusmod tempor</div><p>Lorem ipsum dolor sit amet, consectetur adipiscing elit, sed do eiusmod tempor incididunt ut labore et dolore magna aliqua. Ut enim ad minim veniam, quis nostrud exercitation ullamco laboris nisi ut aliquip ex ea commodo consequat.</p></div>
<div class="job" style="top:1080px"><span class="dot"></span><h3>Lorem ipsum dolor</h3><div class="date">Apr 2020 - Present</div><div class="role">Lorem ipsum dolor sit amet, consectetur adipiscing elit, sed do eiusmod tempor</div><p>Lorem ipsum dolor sit amet, consectetur adipiscing elit, sed do eiusmod tempor incididunt ut labore et dolore magna aliqua. Ut enim ad minim veniam, quis nostrud exercitation ullamco laboris nisi ut aliquip ex ea commodo consequat.</p></div>
<div class="job" style="top:1250px"><span class="dot"></span><h3>Lorem ipsum dolor</h3><div class="date">Apr 2020 - Present</div><div class="role">Lorem ipsum dolor sit amet, consectetur adipiscing elit, sed do eiusmod tempor</div><p>Lorem ipsum dolor sit amet, consectetur adipiscing elit, sed do eiusmod tempor incididunt ut labore et dolore magna aliqua. Ut enim ad minim veniam, quis nostrud exercitation ullamco laboris nisi ut aliquip ex ea commodo consequat.</p></div>
<div class="job" style="top:1420px"><span class="dot"></span><h3>Lorem ipsum dolor</h3><div class="date">Apr 2020 - Present</div><div class="role">Lorem ipsum dolor sit amet, consectetur adipiscing elit, sed do eiusmod tempor</div><p>Lorem ipsum dolor sit amet, consectetur adipiscing elit, sed do eiusmod tempor incididunt ut labore et dolore magna aliqua. Ut enim ad minim veniam, quis nostrud exercitation ullamco laboris nisi ut aliquip ex ea commodo consequat.</p></div>
<div class="job" style="top:1588px"><span class="dot"></span><h3>Lorem ipsum dolor</h3><div class="date">Apr 2020 - Present</div><div class="role">Lorem ipsum dolor sit amet, consectetur adipiscing elit, sed do eiusmod tempor</div><p>Lorem ipsum dolor sit amet, consectetur adipiscing elit, sed do eiusmod tempor incididunt ut labore et dolore magna aliqua. Ut enim ad minim veniam, quis nostrud exercitation ullamco laboris nisi ut aliquip ex ea commodo consequat.</p></div>
<div class="job" style="top:1757px"><span class="dot"></span><h3>Lorem ipsum dolor</h3><div class="date">Apr 2020 - Present</div><div class="role">Lorem ipsum dolor sit amet, consectetur adipiscing elit, sed do eiusmod tempor</div><p>Lorem ipsum dolor sit amet, consectetur adipiscing elit, sed do eiusmod tempor incididunt ut labore et dolore magna aliqua. Ut enim ad minim veniam, quis nostrud exercitation ullamco laboris nisi ut aliquip ex ea commodo consequat.</p></div>

<h2 class="section-title" style="top:1984px">Education</h2>
<div class="cols" style="top:2029px">
  <div class="col"><h4>Lorem ipsum dolor sit amet,</h4><div class="desc">Lorem ipsum dolor sit amet, consectetur adipiscing elit</div><div class="years">2017-2020</div></div>
  <div class="col"><h4>Lorem ipsum dolor sit amet,</h4><div class="desc">Lorem ipsum dolor sit amet, consectetur adipiscing elit</div><div class="years">2017-2020</div></div>
  <div class="col"><h4>Lorem ipsum dolor sit amet,</h4><div class="desc">Lorem ipsum dolor sit amet, consectetur adipiscing elit</div><div class="years">2017-2020</div></div>
</div>

<h2 class="section-title" style="top:2161px">Professional Skills</h2>
<div class="cols" style="top:2212px">
  <div class="col"><svg class="ring" width="88" height="88" viewBox="0 0 88 88"><circle cx="44" cy="44" r="40" fill="none" stroke="var(--ring-gap)" stroke-width="6"/><circle cx="44" cy="44" r="40" fill="none" stroke="var(--orange-ring)" stroke-width="6" stroke-dasharray="246 251" transform="rotate(-86 44 44)"/><text x="44" y="48" text-anchor="middle" font-family="Roboto,sans-serif" font-size="12" fill="var(--orange-ring)">98%</text></svg><h4>Lorem ipsum dolor sit amet,</h4><div class="desc">Lorem ipsum dolor sit amet, consectetur adipiscing elit</div></div>
  <div class="col"><svg class="ring" width="88" height="88" viewBox="0 0 88 88"><circle cx="44" cy="44" r="40" fill="none" stroke="var(--ring-gap)" stroke-width="6"/><circle cx="44" cy="44" r="40" fill="none" stroke="var(--orange-ring)" stroke-width="6" stroke-dasharray="246 251" transform="rotate(-86 44 44)"/><text x="44" y="48" text-anchor="middle" font-family="Roboto,sans-serif" font-size="12" fill="var(--orange-ring)">98%</text></svg><h4>Lorem ipsum dolor sit amet,</h4><div class="desc">Lorem ipsum dolor sit amet, consectetur adipiscing elit</div></div>
  <div class="col"><svg class="ring" width="88" height="88" viewBox="0 0 88 88"><circle cx="44" cy="44" r="40" fill="none" stroke="var(--ring-gap)" stroke-width="6"/><circle cx="44" cy="44" r="40" fill="none" stroke="var(--orange-ring)" stroke-width="6" stroke-dasharray="246 251" transform="rotate(-86 44 44)"/><text x="44" y="48" text-anchor="middle" font-family="Roboto,sans-serif" font-size="12" fill="var(--orange-ring)">98%</text></svg><h4>Lorem ipsum dolor sit amet,</h4><div class="desc">Lorem ipsum dolor sit amet, consectetur adipiscing elit</div><div class="years">2017-2020</div></div>
</div>

<h2 class="section-title" style="top:2414px">Get In Touch</h2>
<p class="touch">Lorem ipsum dolor sit amet, consectetur adipiscing elit, sed do eiusmod tempor incididunt ut labore et dolore magna aliqua. Ut enim ad minim veniam, quis nostrud exercitation ullamco laboris nisi ut aliquip ex ea commodo consequat. Duis aute irure dolor in reprehenderit in voluptate velit esse cillum dolore eu fugiat nulla pariatur. Excepteur sint occæcat cupidatat non proident, sunt in culpa qui officia deserunt mollit anim id est laborum.</p>

<footer class="footer">Copyright © The Company Name. All rights reserved.</footer>
</body>
</html>
```